Real Estate Business Card

On the front side I want to have my info, my brokerage info.
On the back side I want have my complany’s logo, website and Facebook link. I will provide all this once I select a design.

I would like to see Black background and gold text, Dark Blue and gold text and White and blue text designs

Font styles to use
Sans Serif
Script

```html
<!DOCTYPE html>
<html lang="en">
<head>
<meta charset="utf-8">
<title>Northvale Real Estate – Business Card</title>
<link rel="stylesheet" href="https://fonts.googleapis.com/css2?family=Montserrat:wght@800&family=Roboto:wght@400;500;700&display=swap">
<style>
  :root {
    --backdrop: #2a2b2e;
    --card-black: #1c1d20;
    --brand-red: #d42a2f;
    --slate: #7a8396;
    --slate-light: #8d96a8;
    --gold: #e2b94a;
    --icon-yellow: #f1dc7a;
    --white: #ffffff;
    --wordmark-grey: #6d7486;
  }
  * { margin: 0; padding: 0; box-sizing: border-box; }
  html, body { width: 1200px; height: 900px; overflow: hidden; }
  body {
    background: var(--backdrop);
    font-family: "Roboto", Arial, sans-serif;
    position: relative;
  }
  .card {
    position: absolute;
    left: 250px;
    width: 700px;
    height: 400px;
    background: var(--card-black);
    overflow: hidden;
    box-shadow: 0 12px 30px rgba(0,0,0,.45);
  }
  .card--back { top: 40px; }
  .card--front { top: 470px; }

  .brand {
    position: absolute;
    left: 0; right: 0;
    display: flex;
    align-items: center;
    justify-content: center;
    gap: 14px;
    font-family: "Montserrat", Arial, sans-serif;
    font-weight: 800;
    letter-spacing: 1px;
    text-transform: uppercase;
  }
  .brand__mark { display: block; background: var(--brand-red); }
  .card--back .brand { top: 170px; font-size: 46px; color: var(--brand-red); }
  .card--back .brand__mark { width: 40px; height: 40px; }
  .card--front .brand { top: 70px; font-size: 32px; color: var(--wordmark-grey); }
  .card--front .brand__mark { width: 28px; height: 28px; }

  .front-panels { position: absolute; inset: 0; }

  .person {
    position: absolute;
    left: 40px;
    top: 258px;
    color: var(--white);
  }
  .person__name { font-size: 26px; font-weight: 700; color: var(--gold); letter-spacing: .5px; }
  .person__role { font-size: 17px; font-weight: 500; color: var(--gold); margin-bottom: 10px; }
  .person__address { font-size: 17px; line-height: 1.3; font-style: normal; }

  .contacts {
    position: absolute;
    right: 28px;
    top: 278px;
    list-style: none;
    color: var(--white);
    font-size: 17px;
    font-weight: 500;
  }
  .contacts li {
    display: flex;
    align-items: center;
    justify-content: flex-end;
    gap: 10px;
    height: 27px;
  }
  .contacts svg { width: 18px; height: 18px; flex: none; }
</style>
</head>
<body>

<section class="card card--back" aria-label="Card back">
  <div class="brand"><span class="brand__mark"></span>Northvale</div>
</section>

<section class="card card--front" aria-label="Card front">
  <svg class="front-panels" viewBox="0 0 700 400" preserveAspectRatio="none" aria-hidden="true">
    <polygon points="0,190 400,292 376,400 0,400" fill="var(--brand-red)"/>
    <defs>
      <linearGradient id="slateFade" x1="0" x2="1">
        <stop offset="0" stop-color="var(--slate)"/>
        <stop offset="1" stop-color="var(--slate-light)"/>
      </linearGradient>
    </defs>
    <polygon points="400,292 700,262 700,400 376,400" fill="url(#slateFade)"/>
  </svg>

  <div class="brand"><span class="brand__mark"></span>Northvale Real Estate</div>

  <div class="person">
    <p class="person__name">DANA HOLLIS</p>
    <p class="person__role">CEO/FOUNDER</p>
    <address class="person__address">412 Cedar Ridge Road<br>Fairbanks, Alaska 99701</address>
  </div>

  <ul class="contacts">
    <li>555 014 2290
      <svg viewBox="0 0 24 24" aria-hidden="true"><path fill="var(--icon-yellow)" d="M6.6 10.8a15 15 0 0 0 6.6 6.6l2.2-2.2c.3-.3.7-.4 1-.2 1.1.4 2.3.6 3.6.6.6 0 1 .4 1 1V20c0 .6-.4 1-1 1A17 17 0 0 1 3 4c0-.6.4-1 1-1h3.5c.6 0 1 .4 1 1 0 1.3.2 2.5.6 3.6.1.3 0 .7-.2 1z"/></svg>
    </li>
    <li>dana@northvale.com
      <svg viewBox="0 0 24 24" aria-hidden="true"><rect x="2" y="5" width="20" height="14" rx="1" fill="var(--icon-yellow)"/><path d="M3 6l9 7 9-7" stroke="var(--slate)" stroke-width="1.8" fill="none"/></svg>
    </li>
    <li>www.northvale.com
      <svg viewBox="0 0 24 24" aria-hidden="true"><circle cx="12" cy="12" r="10" fill="var(--icon-yellow)"/><path d="M2 12h20M12 2c3 3 3 17 0 20M12 2c-3 3-3 17 0 20" stroke="var(--slate)" stroke-width="1.5" fill="none"/></svg>
    </li>
    <li>/northvale
      <svg viewBox="0 0 24 24" aria-hidden="true"><circle cx="12" cy="12" r="10" fill="var(--icon-yellow)"/></svg>
    </li>
  </ul>
</section>

</body>
</html>
```